Consulting Group Needs a Graphic Design

We have created a unique, cyclical process to describe our company's philosophy on parenting to our clients. It is provided in the attached file. At the center of the graphic design, which includes all written words on the page, is an image of a gardener that we really like. We found it through a clipart service, but we are not able to trademark it as our own. We would like to create a similar image which includes the female gardener tending the garden, with a trowel in her hand and a watering can at her side. We want the flowers in her garden to be different, just as every child is unique and different within the same family. For more perspective on our company, please visit www.brookvalecounsel.com.
Updates

Project Deadline Extended
Reason: Some of the designers are getting very close to what we want. Due to some unforeseen circumstances, we were unable to give feedback for a couple of days. We would really appreciate your consideration of our request. We are eager to get the design finished to move forward with our branding strategy, so we will be hyper-focused on the project over the coming days. Thank you, Willowmere Family Advisors

Project Deadline Extended
Reason: We would like to give our first choice designer a chance to create a complementary logo to accompany his submission. We have been in communication with this designer.

Industry/Entity Type

Gardener

```html
<!DOCTYPE html>
<html lang="en">
<head>
<meta charset="utf-8">
<title>Every Good Gardener – Willowmere Family Advisors</title>
<link rel="stylesheet" href="https://fonts.googleapis.com/css2?family=Marcellus&family=Arimo:wght@400;700&display=swap">
<style>
  :root {
    --page: #ffffff;
    --field-light: #55c21e;
    --field-dark: #178a1a;
    --box-fill: #ffffff;
    --box-edge: #cf3a0c;
    --box-text: #123f12;
    --arrow: #e0582a;
    --title: #ffffff;
    --bush: #2f6e1c;
    --bush-soil: #5a3412;
    --scene-top: #c8743f;
    --scene-mid: #7fb6c4;
    --scene-low: #5c3210;
  }
  html, body {
    margin: 0;
    padding: 0;
    overflow: hidden;
    background: var(--page);
  }
  .canvas {
    position: relative;
    width: 1200px;
    height: 1000px;
    background: var(--page);
    overflow: hidden;
  }
  .field {
    position: absolute;
    left: 55px;
    top: 92px;
    width: 1087px;
    height: 816px;
    background: radial-gradient(ellipse at 50% 50%, var(--field-light) 0%, #43b01c 40%, var(--field-dark) 100%);
  }
  .cycle-arrows {
    position: absolute;
    left: 0;
    top: 0;
  }
  .step {
    position: absolute;
    box-sizing: border-box;
    width: 165px;
    height: 104px;
    background: var(--box-fill);
    border: 5px solid var(--box-edge);
    border-radius: 14px;
    display: flex;
    align-items: center;
    justify-content: center;
    text-align: center;
    font-family: "Arimo", Arial, sans-serif;
    font-weight: 700;
    font-size: 20px;
    line-height: 1.25;
    color: var(--box-text);
  }
  .step--plants   { left: 525px; top: 188px; }
  .step--nurtures { left: 939px; top: 355px; }
  .step--enriches { left: 844px; top: 657px; }
  .step--prunes   { left: 238px; top: 706px; }
  .step--measures { left: 108px; top: 329px; }
  .title {
    position: absolute;
    left: 0;
    width: 1196px;
    top: 352px;
    margin: 0;
    text-align: center;
    font-family: "Marcellus", "Optima", serif;
    font-weight: 400;
    font-size: 47px;
    letter-spacing: 1px;
    color: var(--title);
  }
  .bush {
    position: absolute;
    border-radius: 50%;
    background: radial-gradient(ellipse at 50% 40%, #4f8f22 0%, var(--bush) 60%, var(--bush-soil) 100%);
  }
  .bush--left  { left: 276px; top: 497px; width: 174px; height: 58px; }
  .bush--right { left: 716px; top: 482px; width: 228px; height: 78px; }
  .gardener-scene {
    position: absolute;
    left: 428px;
    top: 440px;
    width: 330px;
    height: 280px;
    border-radius: 40% 40% 30% 30%;
    background: linear-gradient(180deg, var(--scene-top) 0%, var(--scene-mid) 45%, #b04fb8 70%, var(--scene-low) 100%);
    opacity: 0.85;
  }
  .method-name {
    position: absolute;
    left: 440px;
    width: 300px;
    top: 734px;
    margin: 0;
    text-align: center;
    font-family: "Arimo", Arial, sans-serif;
    font-size: 16px;
    letter-spacing: 0.8px;
    color: var(--title);
  }
  .method-name sup { font-size: 9px; }
</style>
</head>
<body>
<div class="canvas">
  <div class="field"></div>

  <svg class="cycle-arrows" width="1200" height="1000" viewBox="0 0 1200 1000" aria-hidden="true">
    <defs>
      <marker id="arrowhead" viewBox="0 0 12 12" refX="9" refY="6" markerWidth="7" markerHeight="7" orient="auto-start-reverse">
        <path d="M1 1 L10 6 L1 11" fill="none" stroke="var(--arrow)" stroke-width="2" stroke-linecap="round" stroke-linejoin="round"/>
      </marker>
    </defs>
    <g fill="none" stroke="var(--arrow)" stroke-width="4" stroke-linecap="round" marker-end="url(#arrowhead)">
      <path d="M248 328 Q340 262 478 245"/>
      <path d="M694 252 Q830 270 925 324"/>
      <path d="M1046 462 Q1066 550 1022 630"/>
      <path d="M842 756 Q660 810 462 790"/>
      <path d="M238 705 Q100 600 124 468"/>
    </g>
  </svg>

  <div class="step step--plants">Plants with<br>purpose</div>
  <div class="step step--nurtures">Nurtures</div>
  <div class="step step--enriches">Enriches<br>the soil</div>
  <div class="step step--prunes">Prunes as<br>needed</div>
  <div class="step step--measures">Measures<br>growth</div>

  <h1 class="title">EVERY GOOD GARDENER:</h1>

  <div class="bush bush--left" role="img" aria-label="Small green shrub on a mound of soil"></div>
  <div class="bush bush--right" role="img" aria-label="Small green shrub on a mound of soil"></div>
  <div class="gardener-scene" role="img" aria-label="Illustration of a red-haired woman kneeling in a flower bed with a trowel, surrounded by varied colourful flowers and a blue watering can"></div>

  <p class="method-name">The Willowmere Growth Method<sup>™</sup></p>
</div>
</body>
</html>
```